Recruiting Firm Need Professional, Modern Tri-Fold Brochure for their United States Based Business

-We need a professional, modern TRI-FOLD brochure design that can help generate business for our recruiting firm. We need an impressive brochure.
- Please use the about us website content and attached website content. Website: www.morvellstaffingpartners.example
- Please use logo files attached.
- Please note: This brochure will be the starting point for an upgraded website design so we are NOT looking for a brochure to look like our current website.
- We want potential clients to want to do business with us just based on the brochure look and feel alone.

Target Market(s)

small, medium, and large companies who need administrative, human resources, and accounting talent

Industry/Entity Type

Professional Service

Font styles to use
Serif

Requirements
Must have
• - Professional, Modern TRI-FOLD Brochure Design for United States Based Company
• - Please show diverse group of professionals pictures similar to the ones on our website. One pic must include an African American female and one pic must include an African male. Or both an African American female and male can be include in the group of other races. But All the group photos must be diverse in race and include both male and female.
• - Please show pics of one business professional too
• a diverse group photo would be nice on the front cover...so we can show diversity and inclusion from the start
Should not have
• - Please DO NOT use the same pictures on our website.

```html
<!DOCTYPE html>
<html lang="en">
<head>
<meta charset="utf-8">
<title>Morvell Staffing Partners – Tri-Fold Brochure</title>
<link rel="stylesheet" href="https://fonts.googleapis.com/css2?family=Open+Sans:wght@400;600&display=swap">
<style>
  :root {
    --stage: #e6e6e6;
    --paper: #ffffff;
    --panel-light: #f4f4f4;
    --brand-red: #a3070d;
    --band-red: #8c0407;
    --band-black: #0e0e0e;
    --footer-dark: #333333;
    --fold-line: #4a4a4a;
    --ink: #1c1c1c;
    --footer-ink: #e2e2e2;
  }
  * { margin: 0; padding: 0; box-sizing: border-box; }
  html, body {
    width: 1200px; height: 923px; overflow: hidden;
    background: var(--stage);
    font-family: "Open Sans", Arial, sans-serif;
  }
  .brochure {
    position: absolute; left: 39px; top: 65px;
    width: 1123px; height: 793px;
    background: var(--paper);
    overflow: hidden;
  }
  .panel-bg-inner {
    position: absolute; left: 374px; top: 0; width: 749px; height: 300px;
    background: var(--panel-light);
  }
  .photo { position: absolute; }
  .photo-professional {
    left: 0; top: 300px; width: 374px; height: 400px;
    background: linear-gradient(160deg, #f3f5f2 0%, #dfe6da 35%, #b9a6ad 60%, #5a4250 85%, #3a2c35 100%);
  }
  .photo-team {
    left: 374px; top: 280px; width: 749px; height: 440px;
    background: linear-gradient(180deg, #f2f2f0 0%, #d9ddd6 25%, #a7a59e 50%, #4b4f5a 75%, #2b2e36 100%);
  }
  .swoosh { position: absolute; left: 0; top: 0; width: 1123px; height: 793px; }

  .about { position: absolute; left: 35px; top: 43px; width: 300px; }
  .about-title {
    color: var(--brand-red); font-weight: 400; font-size: 15px; line-height: 20px;
    margin-bottom: 13px;
  }
  .about-text {
    color: var(--ink); font-size: 11.6px; line-height: 16.35px; text-align: justify;
  }

  .pitch-title {
    position: absolute; left: 415px; top: 34px;
    color: var(--brand-red); font-size: 30.5px; font-weight: 400; letter-spacing: -0.2px;
    white-space: nowrap;
  }
  .benefits { position: absolute; list-style: none; color: var(--ink); font-size: 12.4px; line-height: 16.5px; }
  .benefits-main { left: 415px; top: 93px; width: 300px; }
  .benefits-side { left: 773px; top: 93px; width: 200px; }
  .benefits li { position: relative; padding-left: 23px; }
  .benefits-main li { margin-bottom: 11.5px; }
  .benefits-side li { margin-bottom: 11.5px; }
  .benefits li svg { position: absolute; left: 0; top: 1px; width: 14px; height: 14px; }

  .contact {
    position: absolute; top: 724px; width: 374px; text-align: center; color: var(--footer-ink);
  }
  .contact-left { left: 0; }
  .contact-right { left: 748px; }
  .contact-phone { font-size: 20.5px; font-weight: 400; line-height: 28px; }
  .contact-web { font-size: 14.5px; line-height: 22px; margin-top: 3px; }
  .contact svg { vertical-align: -2px; margin-right: 8px; }
  .contact-phone svg { vertical-align: -1px; }
</style>
</head>
<body>
<main class="brochure">
  <div class="panel-bg-inner"></div>
  <div class="photo photo-professional" role="img" aria-label="Photo of a confident business professional in a suit, arms crossed, in a bright office"></div>
  <div class="photo photo-team" role="img" aria-label="Photo of a diverse team of smiling colleagues reviewing a document together in an office"></div>

  <svg class="swoosh" viewBox="0 0 1123 793" aria-hidden="true">
    <path d="M0,505 C200,640 600,705 1123,622 L1123,793 L0,793 Z" fill="var(--band-black)"/>
    <path d="M0,540 C220,665 620,718 1123,626 L1123,793 L0,793 Z" fill="var(--band-red)"/>
    <path d="M0,578 C240,688 640,735 1123,629 L1123,793 L0,793 Z" fill="#ffffff"/>
    <path d="M0,610 C270,705 670,745 1123,634 L1123,793 L0,793 Z" fill="var(--footer-dark)"/>
    <line x1="374.5" y1="680" x2="374.5" y2="793" stroke="var(--fold-line)" stroke-width="1"/>
    <line x1="748.5" y1="700" x2="748.5" y2="793" stroke="var(--fold-line)" stroke-width="1"/>
  </svg>

  <section class="about">
    <h2 class="about-title">A Top-Notch Resource for Administrative, Human Resources, and Accounting Talent</h2>
    <p class="about-text">Morvell Staffing Partners is a professional search firm that specializes in providing top-notch administrative, human resources, and accounting talent. We provide best-in-class talent to companies seeking to simplify their recruiting process, increase efficiency, and optimize productivity. Each search is customized based on our client's unique requirements. We provide quality, timely, and efficient services. Our recruiters are highly skilled in identifying, screening, interviewing, and assessing candidates across various industries. We develop a partnership with our client and candidate in order to make the recruitment process a success for both parties.</p>
  </section>

  <h1 class="pitch-title">We can find the right talent for your hiring needs.</h1>

  <ul class="benefits benefits-main">
    <li><svg viewBox="0 0 14 14"><path d="M1.5,7.5 L5,11.5 L12.5,1.5" fill="none" stroke="var(--brand-red)" stroke-width="2"/></svg>Top-Notch Talent.&nbsp; We will only present candidates who meet 90% of your job requirements.</li>
    <li><svg viewBox="0 0 14 14"><path d="M1.5,7.5 L5,11.5 L12.5,1.5" fill="none" stroke="var(--brand-red)" stroke-width="2"/></svg>Thorough.&nbsp; We listen to your needs and develop a recruiting checklist to make sure we cover all basis.</li>
    <li><svg viewBox="0 0 14 14"><path d="M1.5,7.5 L5,11.5 L12.5,1.5" fill="none" stroke="var(--brand-red)" stroke-width="2"/></svg>Tenacious.&nbsp; We are passionate and persistent about meeting your expectations.</li>
    <li><svg viewBox="0 0 14 14"><path d="M1.5,7.5 L5,11.5 L12.5,1.5" fill="none" stroke="var(--brand-red)" stroke-width="2"/></svg>Timely.&nbsp; We deliver quality results on time.</li>
    <li><svg viewBox="0 0 14 14"><path d="M1.5,7.5 L5,11.5 L12.5,1.5" fill="none" stroke="var(--brand-red)" stroke-width="2"/></svg>90-Day Placement Guarantee</li>
  </ul>

  <ul class="benefits benefits-side">
    <li><svg viewBox="0 0 14 14"><path d="M1.5,7.5 L5,11.5 L12.5,1.5" fill="none" stroke="var(--brand-red)" stroke-width="2"/></svg>Reasonable Placement Fees</li>
    <li><svg viewBox="0 0 14 14"><path d="M1.5,7.5 L5,11.5 L12.5,1.5" fill="none" stroke="var(--brand-red)" stroke-width="2"/></svg>Simplified Recruiting Process</li>
    <li><svg viewBox="0 0 14 14"><path d="M1.5,7.5 L5,11.5 L12.5,1.5" fill="none" stroke="var(--brand-red)" stroke-width="2"/></svg>Fast, Efficient Service</li>
  </ul>

  <footer class="contact contact-left">
    <p class="contact-phone"><svg width="18" height="18" viewBox="0 0 18 18" aria-hidden="true"><circle cx="9" cy="9" r="8" fill="none" stroke="var(--footer-ink)" stroke-width="1.5"/><path d="M6,5 L7.5,5 L8.2,7 L7.3,7.8 C7.8,9 8.8,10 10,10.6 L10.8,9.7 L12.8,10.4 L12.8,12 C9,12.2 5.8,9 6,5 Z" fill="var(--footer-ink)"/></svg>555-014-0627</p>
    <p class="contact-web"><svg width="12" height="12" viewBox="0 0 12 12" aria-hidden="true"><g fill="none" stroke="var(--footer-ink)" stroke-width="1"><circle cx="6" cy="6" r="5.3"/><ellipse cx="6" cy="6" rx="2.3" ry="5.3"/><line x1="0.7" y1="6" x2="11.3" y2="6"/><line x1="1.5" y1="3.3" x2="10.5" y2="3.3"/><line x1="1.5" y1="8.7" x2="10.5" y2="8.7"/></g></svg>www.morvellstaffingpartners.example</p>
  </footer>

  <footer class="contact contact-right">
    <p class="contact-phone"><svg width="18" height="18" viewBox="0 0 18 18" aria-hidden="true"><circle cx="9" cy="9" r="8" fill="none" stroke="var(--footer-ink)" stroke-width="1.5"/><path d="M6,5 L7.5,5 L8.2,7 L7.3,7.8 C7.8,9 8.8,10 10,10.6 L10.8,9.7 L12.8,10.4 L12.8,12 C9,12.2 5.8,9 6,5 Z" fill="var(--footer-ink)"/></svg>555-014-0627</p>
    <p class="contact-web"><svg width="12" height="12" viewBox="0 0 12 12" aria-hidden="true"><g fill="none" stroke="var(--footer-ink)" stroke-width="1"><circle cx="6" cy="6" r="5.3"/><ellipse cx="6" cy="6" rx="2.3" ry="5.3"/><line x1="0.7" y1="6" x2="11.3" y2="6"/><line x1="1.5" y1="3.3" x2="10.5" y2="3.3"/><line x1="1.5" y1="8.7" x2="10.5" y2="8.7"/></g></svg>www.morvellstaffingpartners.example</p>
  </footer>
</main>
</body>
</html>
```